STICKER DESIGN required for packaging. UK START UP TEA BUSINESS

We are looking for a design for a sticker that will be applied to packaging for our teas! We are a new start up Tea business based in the UK called 'BrookLeafs'
Selling quality loose leaf tea and teabags via our online shop and also face to face at farmers markets / food shows and eventually in our own tea emporium. We will be marketing our teas to hotels, cafes, delis etc. too
We carry every day teas eg. breakfast blends and also speciality and rare teas to offer customers the chance to try something new. Tea as a treat / ritual / indulgence / healthy lifestyle choice / modern
The design will initially be printed on vinyl stickers and then applied to the tea packaging (pouch bags in matte black and matte silver), in the future the design may be printed direct onto our packaging. The sticker design will need to be scalable as the size of the pouch bag varies dependant on the tea.
The sticker we have in mind is a leaf shape (sketch attached)
colour green to match our logo
It will include our logo (files attached)
Text to be included on the sticker is
- www.brookleafs.co.uk
- Welmoor, England
- The tea type eg. Green
It will need to complement both black and silver pouches that we are using to package our teas (see attached image of our pouches)
Colours - green leaf, see our corporate colours (green & orange) on our logo files attached. We also like silver and black.
Font - nothing to swirly, must be easy to read on the packaging
once a sticker design is agreed for the initial tea type (Green) we will require additional files for each tea type that we stock. Just the tea type (Green) to be updated - the rest of the design to stay the same. The tea types we stock are listed below
Green
Black
Oolong
White
Herbal
Blended
Happy to answer any questions and aim to give feedback daily! Thank you for your interest
Best regards

```html
<!DOCTYPE html>
<html lang="en">
<head>
<meta charset="utf-8">
<title>BrookLeafs Green – Leaf Sticker</title>
<link rel="stylesheet" href="https://fonts.googleapis.com/css2?family=Josefin+Sans:wght@300;400&display=swap">
<style>
  :root {
    --leaf-green: #8dc63f;
    --ink-white: #ffffff;
    --backdrop-light: #ffffff;
    --backdrop-edge: #cfcfcf;
  }
  html, body {
    margin: 0;
    padding: 0;
    width: 1200px;
    height: 1000px;
    overflow: hidden;
  }
  .canvas {
    width: 1200px;
    height: 1000px;
    background: radial-gradient(ellipse 62% 58% at 50% 50%, var(--backdrop-light) 55%, var(--backdrop-edge) 100%);
  }
  .sticker { display: block; }
  .leaf-shape { fill: var(--leaf-green); }
  .sticker-text {
    fill: var(--ink-white);
    font-family: "Josefin Sans", "Helvetica Neue", Arial, sans-serif;
  }
  .web-address { font-size: 16px; font-weight: 300; letter-spacing: 1.6px; }
  .location { font-size: 17px; font-weight: 300; letter-spacing: 1.4px; }
  .brand-name { font-size: 44px; font-weight: 300; letter-spacing: 0.5px; }
  .tea-type { font-size: 12px; font-weight: 400; letter-spacing: 5px; }
  .brand-dot { fill: none; stroke: var(--ink-white); stroke-width: 2; }
</style>
</head>
<body>
<main class="canvas">
  <svg class="sticker" width="1200" height="1000" viewBox="0 0 1200 1000" xmlns="http://www.w3.org/2000/svg" aria-label="BrookLeafs Green leaf sticker">
    <path class="leaf-shape" d="
      M 876 262
      C 820 290, 760 300, 660 310
      C 560 320, 470 335, 420 385
      C 365 440, 340 540, 336 640
      C 332 720, 334 770, 344 800
      C 348 812, 356 815, 361 808
      C 364 800, 358 780, 358 750
      C 356 725, 368 708, 392 694
      C 430 672, 520 655, 600 640
      C 700 620, 780 560, 830 460
      C 855 405, 870 340, 888 278
      C 892 264, 884 258, 876 262 Z"/>

    <text class="sticker-text web-address" transform="translate(640 338) rotate(-12.5)">www.brookleafs.co.uk</text>

    <circle class="brand-dot" cx="584" cy="430" r="14"/>
    <text class="sticker-text brand-name" x="584" y="522" text-anchor="middle">BrookLeafs</text>
    <text class="sticker-text tea-type" x="587" y="561" text-anchor="middle">GREEN</text>

    <text class="sticker-text location" transform="translate(395 682) rotate(-14.5)">Welmoor, England</text>
  </svg>
</main>
</body>
</html>
```